Meridale Real Estate

We are looking for help with web design for a new company that is revolutionizing the real estate world on the listing side: by charing per hour for top level professional real estate services. We would like the concept to be simple, clean and easily understood.
Updates

We want this website to actually function, not just a static design.

Industry/Entity Type

Real Estate

```html
<!DOCTYPE html>
<html lang="en">
<head>
<meta charset="utf-8">
<title>Meridale Real Estate</title>
<link href="https://fonts.googleapis.com/css2?family=Raleway:wght@400;500;600&family=Roboto:wght@300;400;500&display=swap" rel="stylesheet">
<style>
:root{
  --purple:#4a2f6b;
  --purple-deep:#3a2356;
  --nav-bg:#ececec;
  --nav-active:#3b3b3b;
  --teal:#1f6f78;
  --teal-dark:#17565e;
  --ink:#333;
  --muted:#777;
  --link:#1f7b86;
  --dark:#1c1c1f;
  --footer:#3c3a3b;
  --footer-base:#242224;
  --white:#fff;
}
*{margin:0;padding:0;box-sizing:border-box}
html,body{width:730px;height:1200px;overflow:hidden}
body{position:relative;background:var(--white);font-family:'Roboto',Arial,sans-serif;color:var(--ink)}
.abs{position:absolute}

.header{left:0;top:0;width:730px;height:70px;background:var(--purple)}
.brand{left:0;top:0;width:730px;height:70px;display:flex;align-items:center;justify-content:center;gap:8px}
.brand-dot{width:10px;height:10px;border-radius:50%;background:var(--white)}
.brand-name{font-family:'Raleway',sans-serif;font-weight:500;font-size:15px;letter-spacing:3px;color:var(--white);text-transform:uppercase}

.nav{left:0;top:70px;width:730px;height:32px;background:var(--nav-bg);border-bottom:1px solid #d6d6d6}
.nav ul{list-style:none;position:absolute;left:68px;top:0;height:32px;display:flex}
.nav li{font-size:7.4px;line-height:32px;padding:0 13.5px;color:#333;text-transform:uppercase;white-space:nowrap}
.nav li.active{background:var(--nav-active);color:var(--white);padding:0 11px}

.hero{left:0;top:102px;width:730px;height:268px;background:linear-gradient(180deg,#3b2a5a 0%,#2d2346 30%,#3a3046 55%,#2a2a22 80%,#1f2318 100%)}
.hero-title{left:0;top:200px;width:730px;text-align:center;font-family:'Roboto',sans-serif;font-weight:400;font-size:27px;color:var(--white);letter-spacing:.5px}
.hero-text{left:135px;top:237px;width:460px;text-align:center;font-size:9.4px;line-height:13px;color:var(--white)}
.dots{left:350px;top:349px;display:flex;gap:7px}
.dots span{width:6px;height:6px;border-radius:50%;background:rgba(255,255,255,.25)}
.dots span.on{background:var(--white)}

.section-title{left:0;width:730px;text-align:center;font-family:'Raleway',sans-serif;font-weight:500;font-size:12.5px;letter-spacing:.3px}
.feature-title{top:390px;color:#333}

.card{top:423px;width:137px;height:170px;box-shadow:0 4px 6px rgba(0,0,0,.25)}
.card-photo{position:absolute;left:0;top:0;width:137px;height:91px}
.card-body{position:absolute;left:0;top:91px;width:137px;height:79px;background:linear-gradient(180deg,var(--teal),var(--teal-dark));padding:8px 10px 0 12px}
.card-body h3{font-family:'Raleway',sans-serif;font-weight:500;font-size:8.2px;line-height:12px;color:var(--white);text-transform:uppercase}
.card-body p{font-size:6.4px;line-height:12.4px;color:#d9ecee;margin-top:3px}

.services{left:0;top:619px;width:730px;height:264px;background:linear-gradient(180deg,#232325,#1a1b1d 60%,#202123)}
.services-title{top:645px;color:var(--white)}
.service{top:0;width:186px}
.service-photo{position:absolute;top:677px;width:85px;height:85px;border-radius:50%;border:2px solid #2b8a8f}
.service-rule{position:absolute;height:0;border-top:1.5px dotted #cfcfcf}
.service-name{position:absolute;top:783px;text-align:center;font-size:9.4px;color:var(--white);text-transform:uppercase;letter-spacing:.3px}
.service-text{position:absolute;top:814px;text-align:center;font-size:6.8px;line-height:12.4px;color:#ddd}

.col-title{top:901px;font-family:'Raleway',sans-serif;font-weight:500;font-size:12.5px;color:#333;border-bottom:1px solid #ddd;padding-bottom:6px}
.news{left:68px;width:189px;height:78px;background:#ececec;box-shadow:0 1px 2px rgba(0,0,0,.12)}
.news-photo{position:absolute;left:9px;top:10px;width:69px;height:50px}
.news h4{position:absolute;left:85px;top:12px;width:100px;font-weight:400;font-size:7.2px;line-height:12px;color:var(--link)}
.news p{position:absolute;left:85px;top:36px;width:102px;font-size:6.6px;line-height:11.5px;color:var(--muted);white-space:nowrap;overflow:hidden}

.map{left:318px;top:950px;width:90px;height:52px;background:radial-gradient(ellipse at center,#e6eaee 0%,#f4f6f8 60%,transparent 75%)}
.contact-line{left:285px;font-size:7px;color:#555;line-height:12px}
.contact-icon{left:272px}
.follow{left:272px;top:1036px;font-size:7px;color:var(--link);letter-spacing:.3px}
.socials{left:272px;top:1052px;display:flex;gap:4px}
.socials span{width:18px;height:18px;border-radius:50%;background:#4b4b55}

.cw-login{left:475px;top:932px;width:30px;height:14px;background:#4e5f96;border:1px solid #3b4b7c;color:var(--white);font-size:7px;font-weight:500;line-height:12px;text-align:center}
.cw-note{left:511px;top:932px;width:150px;font-size:5.4px;line-height:7.5px;color:#888}
.cw-rule{left:474px;width:188px;border-top:1px solid #e2e2e2}
.cw-item{left:474px;width:188px;height:24px}
.cw-thumb{position:absolute;left:0;top:0;width:23px;height:22px;background:linear-gradient(135deg,#2a7d83,#17565e)}
.cw-item h5{position:absolute;left:28px;top:0;width:160px;font-weight:400;font-size:5.8px;line-height:6.6px;color:#2b4d8c}
.cw-item p{position:absolute;left:28px;font-size:4.6px;color:#888}
.cw-plugin{left:475px;top:1082px;font-size:4.8px;color:#555;display:flex;align-items:center;gap:3px}
.cw-plugin i{width:7px;height:7px;background:#4e5f96;display:block}

.footer-nav{left:0;top:1120px;width:730px;height:42px;background:var(--footer)}
.footer-nav ul{list-style:none;display:flex;justify-content:center;gap:20px;line-height:42px;margin-left:-6px}
.footer-nav li{font-size:7px;color:#cfcfcf}
.footer-base{left:0;top:1162px;width:730px;height:38px;background:var(--footer-base);border-bottom:2px solid var(--teal)}
.footer-base p{text-align:center;line-height:36px;font-size:6.6px;font-weight:500;color:var(--white)}
</style>
</head>
<body>

<header class="abs header">
  <div class="abs brand"><span class="brand-dot"></span><span class="brand-name">Meridale Real Estate</span></div>
</header>

<nav class="abs nav">
  <ul>
    <li class="active">Home</li>
    <li>Company Profile</li>
    <li>Management Services</li>
    <li>Owners Information</li>
    <li>Tenant Information</li>
    <li>Properties</li>
    <li>About Darwin</li>
  </ul>
</nav>

<section class="abs hero" role="img" aria-label="Night view of a waterfront city with lit apartment towers, a marina and park trees"></section>
<h1 class="abs hero-title">TENANT INFORMATION</h1>
<p class="abs hero-text">Lorem ipsum dolor sit amet, consectetuer adipiscing elit, sed diam nonummy nibh euismod tincidunt ut laoreet dolore magna aliquam erat volutpat.</p>
<div class="abs dots"><span></span><span class="on"></span><span></span></div>

<h2 class="abs section-title feature-title">FEATURE PROPERTIES</h2>

<article class="abs card" style="left:68px">
  <div class="card-photo" role="img" aria-label="Modern house with lit swimming pool at dusk" style="background:linear-gradient(180deg,#1b2a4a 0%,#3b4a5e 45%,#1fa9d6 70%,#5b5a5a 100%)"></div>
  <div class="card-body"><h3>Cum sociis natoque pen atibus et</h3><p>Lorem ipsum dolor sit amet, consectetuer adipiscing elit, sed diam nonummy nibh</p></div>
</article>
<article class="abs card" style="left:220px">
  <div class="card-photo" role="img" aria-label="White modern villa beside a reflecting pool" style="background:linear-gradient(180deg,#6f9fc4 0%,#d6dde2 45%,#e9eef0 65%,#3a5d6e 100%)"></div>
  <div class="card-body"><h3>Ut wisi enim ad minim ven iam quis nostrud</h3><p>Lorem ipsum dolor sit amet, consectetuer adipiscing elit, sed diam nonummy nibh</p></div>
</article>
<article class="abs card" style="left:373px">
  <div class="card-photo" role="img" aria-label="Red brick two storey family home with lawn" style="background:linear-gradient(180deg,#5e93c9 0%,#8eb6da 35%,#9a5a48 60%,#4f7d2e 100%)"></div>
  <div class="card-body"><h3>Duis autem vel eum iriure dolor in hendr</h3><p>Lorem ipsum dolor sit amet, consectetuer adipiscing elit, sed diam nonummy nibh</p></div>
</article>
<article class="abs card" style="left:525px">
  <div class="card-photo" role="img" aria-label="Cream house with red tiled roof and double garage" style="background:linear-gradient(180deg,#f4f7f9 0%,#c7603f 35%,#e6dcc4 60%,#5c7a34 100%)"></div>
  <div class="card-body"><h3>Mirum est notare quam littera gothica</h3><p>Lorem ipsum dolor sit amet, consectetuer adipiscing elit, sed diam nonummy nibh</p></div>
</article>

<section class="abs services" role="img" aria-label="Darkened aerial view of a harbour suburb"></section>
<h2 class="abs section-title services-title">OUR SERVICES</h2>

<div class="service-photo" role="img" aria-label="Businessman touching a house outline" style="left:120px;background:radial-gradient(circle,#3d6f8f,#0f2436)"></div>
<div class="service-photo" role="img" aria-label="Company emblem on a light background" style="left:323px;background:#e9e6e1"></div>
<div class="service-photo" role="img" aria-label="White weatherboard house" style="left:526px;background:linear-gradient(180deg,#dfe7ee,#b5b9be 50%,#6a7e4a)"></div>

<div class="service-rule" style="left:68px;width:186px;top:774px"></div>
<div class="service-rule" style="left:68px;width:186px;top:805px"></div>
<div class="service-rule" style="left:271px;width:186px;top:774px"></div>
<div class="service-rule" style="left:271px;width:186px;top:805px"></div>
<div class="service-rule" style="left:474px;width:188px;top:774px"></div>
<div class="service-rule" style="left:474px;width:188px;top:805px"></div>

<h3 class="service-name" style="left:68px;width:186px">Management Services</h3>
<h3 class="service-name" style="left:271px;width:186px">Owners Information</h3>
<h3 class="service-name" style="left:474px;width:188px">Tenant Information</h3>
<p class="service-text" style="left:66px;width:190px">Lorem ipsum dolor sit amet, consectetuer adipiscing elit, sed diam nonummy nibh euismod tincidunt ut laoreet dolore magna aliquam erat volutpat.</p>
<p class="service-text" style="left:270px;width:190px">Ut wisi enim ad minim veniam, quis nostrud exerci tation ullamcorper suscipit lobortis nisl ut aliquip ex ea commodo consequat.</p>
<p class="service-text" style="left:472px;width:192px">Duis autem vel eum iriure dolor in hendrerit in vulputate velit esse molestie consequat, vel illum dolore eu feugiat nulla facilisis at vero eros et accumsan et.</p>

<h2 class="abs col-title" style="left:68px;width:189px">LATEST NEWS</h2>
<h2 class="abs col-title" style="left:270px;width:188px">CONTACT US</h2>
<h2 class="abs col-title" style="left:474px;width:188px">CIRCLEWALL</h2>

<article class="abs news" style="top:930px">
  <div class="news-photo" role="img" aria-label="Brick suburban house" style="background:linear-gradient(180deg,#9cc3e0,#a55a3c 55%,#6b8a3a)"></div>
  <h4>Lorem ipsum dolor sit amet, consectetuer adipiscing..</h4>
  <p>Ut wisi enim ad minim veniam,<br>quis nostrud exerci tation ullamc<br>orper suscipit...</p>
</article>
<article class="abs news" style="top:1019px">
  <div class="news-photo" role="img" aria-label="Dark two storey townhouse" style="background:linear-gradient(180deg,#a9c9e2,#3d3f48 50%,#5b7a3a)"></div>
  <h4>Ut wisi enim ad minim veniam, quis nostrud exerci tation</h4>
  <p>Ut wisi enim ad minim veniam,<br>quis nostrud exerci tation ullamc<br>orper suscipit...</p>
</article>

<div class="abs map" role="img" aria-label="Faint world map"></div>
<svg class="abs contact-icon" style="top:940px" width="8" height="10" viewBox="0 0 8 10"><path d="M4 0a3.5 3.5 0 0 0-3.5 3.5C.5 6 4 10 4 10s3.5-4 3.5-6.5A3.5 3.5 0 0 0 4 0z" fill="var(--teal)"/><circle cx="4" cy="3.5" r="1.3" fill="#fff"/></svg>
<div class="abs contact-line" style="top:940px;color:var(--link)">NOW LEASING</div>
<div class="abs contact-line" style="top:952px">123 Lorem Ipsm ., Lorem IPsm, Lorem Ipsm,<br>Lorem Ipsm - 123 456</div>
<svg class="abs contact-icon" style="top:981px" width="9" height="7" viewBox="0 0 9 7"><rect width="9" height="7" rx="1" fill="var(--teal)"/><path d="M.5 .8 4.5 4l4-3.2" stroke="#fff" stroke-width=".9" fill="none"/></svg>
<div class="abs contact-line" style="top:979px">info@meridale-homes.com</div>
<svg class="abs contact-icon" style="top:1001px" width="9" height="9" viewBox="0 0 9 9"><rect width="9" height="9" rx="1.5" fill="var(--teal)"/><path d="M3 2c-.8.5-.9 1.6.2 3s2.4 2.3 3.2 1.6l-.9-1.1-.8.4L3.5 4.2l.4-.8z" fill="#fff"/></svg>
<div class="abs contact-line" style="top:999px">123 456 789</div>
<div class="abs follow">FOLLOW ON :</div>
<div class="abs socials" aria-label="Social network links"><span></span><span></span><span></span><span></span><span></span></div>

<div class="abs cw-login">Login</div>
<p class="abs cw-note">You need to be logged into to see your friends'<br>activity</p>
<div class="abs cw-rule" style="top:954px"></div>
<div class="abs cw-item" style="top:964px"><div class="cw-thumb"></div><h5>Lorem ipsum dolor sit amet, consectetuer adipiscing elit, sed diam nonummy nibh euismod</h5><p style="top:15px">6 people recommend this.</p></div>
<div class="abs cw-item" style="top:1002px"><div class="cw-thumb"></div><h5>Ut wisi enim ad minim veniam, quis nostrud exerci tation ullamcorper suscipit</h5><p style="top:15px">6 people recommend this.</p></div>
<div class="abs cw-item" style="top:1039px"><div class="cw-thumb"></div><h5>Lorem ipsum dolor sit amet, consectetuer adipiscing elit, sed diam nonummy nibh euismod</h5><p style="top:15px">6 people recommend this.</p></div>
<div class="abs cw-rule" style="top:1072px"></div>
<div class="abs cw-plugin"><i></i>Circlewall social plugin</div>

<footer class="abs footer-nav">
  <ul>
    <li>Home</li><li>Company Profile</li><li>Management Services</li><li>Owners information</li><li>Tenant information</li><li>Properties</li><li>About Darwin</li>
  </ul>
</footer>
<div class="abs footer-base"><p>© Copyrights 2015 Meridale Real Estate. All Right Reserved</p></div>

</body>
</html>
```